New Business card design to reflect rebrand

I would like a business card design with a good base colour for our new logo and also a placeholder for a profile pic of the card holder. the design needs to be editable to the point that we can easily change the picture of the person and use that design for printmerlo etc. we are looking at a metalic finish business card so will need a good base colour to bring out the finish.

Target Market(s)

prospective customers

Industry/Entity Type

Business

Contact Information for Business Card

I would like one editable design that we can change the name of the card holder and profile picture. The design need to be in a format that be send to printmerlo etc.

Our address is Fenwick Lodge, Copse Lane, Ashcombe Vale, GU14 3TP Tel no. 01483 556172

Requirements
Must have
• place holder for a profile pic for the card holder. in AI or preferably PSD format

```html
<!DOCTYPE html>
<html lang="en">
<head>
<meta charset="utf-8">
<title>Halvern Workplace Services – Business Card</title>
<link rel="stylesheet" href="https://fonts.googleapis.com/css2?family=Tinos:wght@400;700&display=swap">
<style>
  :root {
    --page-bg: #e9e7e3;
    --card-white: #f7f7f5;
    --brand-blue: #3b5578;
    --brand-blue-deep: #2c4566;
    --brand-blue-light: #5f7fa5;
    --brand-orange: #e97a22;
    --photo-light: #d9dcdf;
    --photo-mid: #a9afb5;
    --photo-dark: #3a3f47;
  }
  * { box-sizing: border-box; margin: 0; padding: 0; }
  html, body { width: 1200px; height: 902px; overflow: hidden; }
  body {
    background: var(--page-bg);
    font-family: "Tinos", "Times New Roman", serif;
    position: relative;
  }
  .card {
    position: absolute;
    top: 296px;
    width: 540px;
    height: 309px;
    border-radius: 3px;
    overflow: hidden;
    box-shadow: 0 6px 18px rgba(0,0,0,0.18);
  }
  .card-front { left: 40px; background: var(--card-white); }
  .card-back {
    left: 620px;
    background: linear-gradient(135deg, var(--brand-blue-light) 0%, var(--brand-blue) 45%, var(--brand-blue-deep) 100%);
  }

  /* Front: brand and contact */
  .brand {
    position: absolute;
    left: 34px;
    top: 40px;
    display: flex;
    align-items: center;
    gap: 10px;
  }
  .brand-mark { width: 22px; height: 22px; background: var(--brand-orange); }
  .brand-name {
    font-weight: 700;
    font-size: 26px;
    letter-spacing: 1px;
    color: var(--brand-blue);
    line-height: 1;
  }
  .brand-tagline {
    position: absolute;
    left: 66px;
    top: 72px;
    font-size: 11px;
    letter-spacing: 2.5px;
    color: var(--brand-blue);
    text-transform: uppercase;
  }
  .contact {
    position: absolute;
    left: 34px;
    top: 140px;
    color: var(--brand-orange);
    font-size: 15px;
    line-height: 1.45;
  }
  .contact-address { margin-bottom: 12px; }
  .contact-row { display: flex; }
  .contact-label { width: 26px; }

  /* Front: dividing bands */
  .band { position: absolute; top: 0; bottom: 0; }
  .band-orange { left: 330px; width: 9px; background: var(--brand-orange); }
  .band-blue { left: 343px; width: 7px; background: var(--brand-blue); }

  /* Front: profile photo area */
  .profile-photo {
    position: absolute;
    left: 350px;
    top: 0;
    right: 0;
    bottom: 0;
    background: linear-gradient(160deg, var(--photo-light) 0%, var(--photo-mid) 55%, var(--photo-dark) 100%);
  }
  .holder {
    position: absolute;
    left: 350px;
    right: 0;
    bottom: 22px;
    padding: 8px 14px;
    background: rgba(235,238,241,0.72);
    text-align: right;
    color: var(--brand-blue-deep);
  }
  .holder-name { font-size: 17px; font-weight: 700; }
  .holder-position { font-size: 14px; }

  /* Back */
  .web {
    position: absolute;
    left: 30px;
    top: 30px;
    color: #ffffff;
    font-size: 15px;
    letter-spacing: 0.5px;
  }
  .back-brand {
    position: absolute;
    left: 0;
    right: 0;
    top: 118px;
    text-align: center;
    color: #ffffff;
    font-weight: 700;
    font-size: 68px;
    letter-spacing: 4px;
    line-height: 1;
  }
</style>
</head>
<body>
  <section class="card card-front" aria-label="Business card front">
    <div class="brand">
      <span class="brand-mark"></span>
      <span class="brand-name">HALVERN</span>
    </div>
    <div class="brand-tagline">Workplace Services</div>

    <div class="contact">
      <p class="contact-address">Fenwick Lodge, Copse Lane,<br>Ashcombe Vale, GU14 3TP</p>
      <p class="contact-row"><span class="contact-label">T</span><span>: 01483 556172</span></p>
      <p class="contact-row"><span class="contact-label">M</span><span>: 07700 900418</span></p>
      <p class="contact-row"><span class="contact-label">E</span><span>: name@halvernwork.co.uk</span></p>
    </div>

    <div class="band band-orange"></div>
    <div class="band band-blue"></div>

    <div class="profile-photo" role="img" aria-label="Profile photo of the card holder"></div>
    <div class="holder">
      <p class="holder-name">Name surname</p>
      <p class="holder-position">Your Position</p>
    </div>
  </section>

  <section class="card card-back" aria-label="Business card back">
    <p class="web">www.halvernwork.co.uk</p>
    <p class="back-brand">HALVERN</p>
  </section>
</body>
</html>
```